Alcohol brand needs design for gift tin packaging

We need a new design for the gift tins for our vodka brand. The bottles are in the shape of an oil barrel and the tins are also in the same shape. We would like to see the use of our logo. The gift tin needs to have a premium look.
Images of our bottles, logo and the gift tin are attached.

```html
<!DOCTYPE html>
<html lang="en">
<head>
<meta charset="utf-8">
<title>Copper Drum Vodka – Gift Tin Label</title>
<link rel="stylesheet" href="https://fonts.googleapis.com/css2?family=Staatliches&family=Special+Elite&display=swap">
<style>
  :root {
    --paper: #ffffff;
    --tin-light: #f1f1f1;
    --tin-mid: #dedede;
    --tin-dark: #c9c9c9;
    --brown-dark: #4a2614;
    --brown: #6b3a1f;
    --copper: #b5541c;
    --copper-light: #c8652a;
    --cream: #e9d7c6;
  }
  * { box-sizing: border-box; margin: 0; padding: 0; }
  html, body {
    width: 1149px;
    height: 1200px;
    overflow: hidden;
    background: var(--paper);
  }
  .canvas {
    position: relative;
    width: 1149px;
    height: 1200px;
    background: var(--paper);
  }

  /* Brand lockup above the tin face */
  .brand-lockup {
    position: absolute;
    top: 110px;
    left: 0;
    width: 100%;
    display: flex;
    align-items: center;
    justify-content: center;
    gap: 22px;
  }
  .brand-lockup__dot {
    width: 74px;
    height: 74px;
    border-radius: 50%;
    background: var(--brown);
  }
  .brand-lockup__name {
    font-family: "Staatliches", sans-serif;
    font-size: 76px;
    letter-spacing: 4px;
    color: var(--brown);
    line-height: 1;
  }

  /* Flat tin face */
  .tin-face {
    position: absolute;
    top: 300px;
    left: 224px;
    width: 700px;
    height: 860px;
    border-radius: 14px;
    background: linear-gradient(90deg, var(--tin-dark) 0%, var(--tin-light) 30%, var(--tin-light) 65%, var(--tin-mid) 100%);
    overflow: hidden;
  }
  .tin-face__name {
    position: absolute;
    top: 70px;
    width: 100%;
    text-align: center;
    font-family: "Staatliches", sans-serif;
    font-size: 112px;
    letter-spacing: 6px;
    color: var(--brown);
    line-height: 1;
  }
  .tin-face__type {
    position: absolute;
    top: 200px;
    width: 100%;
    text-align: center;
    font-family: "Staatliches", sans-serif;
    font-size: 84px;
    letter-spacing: 5px;
    color: var(--brown-dark);
    line-height: 1;
  }

  .ribbon {
    position: absolute;
    top: 400px;
    left: 40px;
    width: 620px;
    height: 130px;
    background: linear-gradient(90deg, var(--brown-dark), var(--copper));
    display: flex;
    align-items: center;
    justify-content: space-between;
    padding: 0 36px;
    clip-path: polygon(0 8%, 100% 0, 100% 92%, 0 100%);
  }
  .ribbon__text {
    font-family: "Staatliches", sans-serif;
    color: var(--cream);
    text-align: center;
    line-height: 0.9;
  }
  .ribbon__small { font-size: 40px; letter-spacing: 2px; display: block; }
  .ribbon__big { font-size: 60px; display: block; }
  .ribbon__tiny { font-size: 30px; letter-spacing: 1px; display: block; }

  .emblem {
    position: absolute;
    top: 335px;
    left: 225px;
    width: 250px;
    height: 250px;
  }

  .tin-face__style {
    position: absolute;
    top: 625px;
    width: 100%;
    text-align: center;
    font-family: "Special Elite", monospace;
    font-size: 40px;
    color: var(--brown-dark);
  }
  .tin-face__warning {
    position: absolute;
    top: 680px;
    width: 100%;
    text-align: center;
    font-family: "Staatliches", sans-serif;
    font-size: 70px;
    letter-spacing: 4px;
    color: var(--brown-dark);
    line-height: 1;
  }
  .tin-face__band {
    position: absolute;
    bottom: 0;
    left: 0;
    width: 100%;
    height: 84px;
    background: linear-gradient(90deg, var(--brown-dark), var(--copper-light) 55%, var(--brown));
    display: flex;
    align-items: center;
    justify-content: center;
    font-family: "Special Elite", monospace;
    font-size: 34px;
    letter-spacing: 2px;
    color: var(--cream);
  }
</style>
</head>
<body>
<main class="canvas">
  <header class="brand-lockup">
    <span class="brand-lockup__dot"></span>
    <span class="brand-lockup__name">COPPER DRUM</span>
  </header>

  <section class="tin-face">
    <h1 class="tin-face__name">COPPER DRUM</h1>
    <p class="tin-face__type">VODKA</p>

    <div class="ribbon">
      <p class="ribbon__text">
        <span class="ribbon__small">SINCE</span>
        <span class="ribbon__big">2017</span>
      </p>
      <p class="ribbon__text">
        <span class="ribbon__big">40%</span>
        <span class="ribbon__tiny">ALCOHOL</span>
      </p>
    </div>

    <svg class="emblem" viewBox="0 0 250 250" role="img" aria-label="Brand emblem artwork area">
      <defs>
        <linearGradient id="emblemFill" x1="0" y1="0" x2="1" y2="1">
          <stop offset="0" stop-color="#6b3a1f"/>
          <stop offset="1" stop-color="#b5541c"/>
        </linearGradient>
      </defs>
      <circle cx="125" cy="125" r="122" fill="url(#emblemFill)"/>
    </svg>

    <p class="tin-face__style">Single Malt</p>
    <p class="tin-face__warning">DRINK CAUTIOUSLY</p>

    <footer class="tin-face__band">PREMIUM AUSTRALIAN VODKA</footer>
  </section>
</main>
</body>
</html>
```